Corvenna Climate Business Card Design

Design new, 2 sides, business cards for a residential and light commercial heating, air conditioning contractor.

Target Market(s)

Homeowners, small businesses

Industry/Entity Type

Business

Contact Information for Business Card

Dominic Westerhall
Phone - 862-415-2736
Email
Address - PO box 518
Brightwater NJ 07912
Website - www.CorvennaClimateLLC.example

Requirements
Must have
• logo, company colors, standard size with no die cut, so I can use nova stamp

```html
<!DOCTYPE html>
<html lang="en">
<head>
<meta charset="utf-8">
<title>Corvenna Climate Business Card</title>
<link href="https://fonts.googleapis.com/css2?family=Lato:wght@400;700&display=swap" rel="stylesheet">
<style>
  :root {
    --crimson: #a32a40;
    --crimson-light: #b8485a;
    --crimson-dark: #8e1f34;
    --orange: #ea8a2c;
    --text-grey: #5a5a5a;
    --rule-grey: #9a9a9a;
    --paper: #ffffff;
    --stage: #e9e6e1;
    --cream: #f7dca9;
  }
  * { margin: 0; padding: 0; box-sizing: border-box; }
  html, body { width: 1200px; height: 1023px; overflow: hidden; }
  body {
    background: var(--stage);
    font-family: 'Lato', sans-serif;
    position: relative;
  }
  .card {
    position: absolute;
    left: 220px;
    width: 760px;
    height: 434px;
    border-radius: 4px;
    box-shadow: 0 6px 18px rgba(0,0,0,0.18);
    overflow: hidden;
  }
  .card-front { top: 50px; background: var(--paper); }
  .card-back {
    top: 520px;
    background: linear-gradient(120deg, var(--crimson-light) 0%, var(--crimson) 45%, var(--crimson-dark) 100%);
  }

  .brand-mark {
    position: absolute;
    display: flex;
    align-items: center;
    gap: 12px;
    white-space: nowrap;
  }
  .brand-dot {
    width: 20px; height: 20px;
    border-radius: 50%;
    background: var(--orange);
    flex: none;
  }
  .brand-name {
    font-weight: 700;
    color: var(--crimson);
  }

  /* front */
  .card-front .brand-mark { left: 44px; top: 110px; }
  .card-front .brand-name { font-size: 30px; }
  .holder-name {
    position: absolute;
    right: 60px;
    top: 176px;
    font-weight: 700;
    font-size: 30px;
    line-height: 1;
    color: var(--crimson);
    white-space: nowrap;
  }
  .divider {
    position: absolute;
    left: 200px;
    right: 60px;
    top: 222px;
    height: 1px;
    background: var(--rule-grey);
  }
  .address {
    position: absolute;
    left: 200px;
    top: 240px;
    display: flex;
    gap: 10px;
    color: var(--text-grey);
    font-size: 18px;
    line-height: 1.35;
    white-space: nowrap;
  }
  .contact-list {
    position: absolute;
    right: 36px;
    top: 238px;
    list-style: none;
    color: var(--text-grey);
    font-size: 18px;
    line-height: 1.5;
  }
  .contact-list li {
    display: flex;
    justify-content: flex-end;
    align-items: center;
    gap: 10px;
    white-space: nowrap;
  }
  .icon { width: 15px; height: 15px; flex: none; }

  /* back */
  .card-back .brand-mark {
    left: 0; right: 0;
    top: 190px;
    justify-content: center;
    gap: 14px;
  }
  .card-back .brand-name { color: var(--cream); font-size: 42px; }
  .back-website {
    position: absolute;
    left: 80px;
    bottom: 40px;
    color: #f3e6e8;
    font-size: 18px;
    letter-spacing: 0.3px;
  }
</style>
</head>
<body>

<section class="card card-front" aria-label="Business card front">
  <div class="brand-mark">
    <span class="brand-dot"></span>
    <span class="brand-name">Corvenna Climate</span>
  </div>

  <h1 class="holder-name">Dominic Westerhall</h1>
  <div class="divider"></div>

  <div class="address">
    <svg class="icon" viewBox="0 0 16 16" style="margin-top:4px"><path fill="var(--orange)" d="M8 1a5 5 0 0 0-5 5c0 3.6 5 9 5 9s5-5.4 5-9a5 5 0 0 0-5-5zm0 7a2 2 0 1 1 0-4 2 2 0 0 1 0 4z"/></svg>
    <p>PO box 518<br>Brightwater NJ 07912</p>
  </div>

  <ul class="contact-list">
    <li>862-415-2736
      <svg class="icon" viewBox="0 0 16 16"><path fill="var(--orange)" d="M3.5 1.5l2.5 0 1 3.5-1.8 1.2c.8 1.8 2.2 3.2 4 4l1.2-1.8 3.5 1v2.5c0 .8-.7 1.5-1.5 1.5C6.6 13.4 2.6 9.4 2 3c0-.8.7-1.5 1.5-1.5z"/></svg>
    </li>
    <li>info@CorvennaClimateLLC.example
      <svg class="icon" viewBox="0 0 16 16"><rect x="1" y="3" width="14" height="10" rx="1" fill="var(--orange)"/><path d="M1.5 3.5L8 9l6.5-5.5" fill="none" stroke="#fff" stroke-width="1.3"/></svg>
    </li>
    <li>www.CorvennaClimateLLC.example
      <svg class="icon" viewBox="0 0 16 16"><circle cx="8" cy="8" r="6.5" fill="none" stroke="var(--orange)" stroke-width="1.4"/><ellipse cx="8" cy="8" rx="2.8" ry="6.5" fill="none" stroke="var(--orange)" stroke-width="1.2"/><path d="M1.5 8h13M2.5 5h11M2.5 11h11" stroke="var(--orange)" stroke-width="1"/></svg>
    </li>
  </ul>
</section>

<section class="card card-back" aria-label="Business card back">
  <div class="brand-mark">
    <span class="brand-dot"></span>
    <span class="brand-name">Corvenna Climate</span>
  </div>
  <p class="back-website">www.CorvennaClimateLLC.example</p>
</section>

</body>
</html>
```